Laser Tattoo Removal Business Cards

We are looking for a professional business card design for a laser tattoo removal business. Ideally looking for a black business card design. The name of the business is Brightline Tattoo Removal. We place our cards at local tattoo shops so we ideally are looking for something trendy/edgy to draw both male and female clientele in.

Target Market(s)

Male/Female ages 18-60

Contact Information for Business Card

black background ideally.. hoping to stay within greys, whites and black

Font styles to use
Serif
Sans Serif

Colors
121212
a9a9a9
5c5c5c
f5f5f5
ffffff
7f7f7f
606060
848484
9d9d9d

Requirements
Must have
• Employee Info:
• Melissa Thornbury
• Chief Executive Offer
• m: 919.537.2846
• w: 919.362.4178
• f: 919.685.3907
• mthornbury@brightlinetattooremoval.example
• Address:
• 4615 Oakmere Pkwy, Suite 210
• Raleigh, NC 27654
• Website:
• www.brightlinetattooremoval.example
Nice to have
• Myabe business name on back or logo on back and employee info on the front

```html
<!DOCTYPE html>
<html lang="en">
<head>
<meta charset="utf-8">
<title>Brightline Tattoo Removal – Business Card</title>
<link rel="stylesheet" href="https://fonts.googleapis.com/css2?family=Roboto:wght@400;500&family=Roboto+Condensed:wght@500&display=swap">
<style>
  :root {
    --stage: #e4e1dc;
    --card-black: #000000;
    --card-white: #f5f5f5;
    --ink-white: #ffffff;
    --ink-dark: #2a2a2a;
    --ink-grey: #5c5c5c;
    --shadow: rgba(0, 0, 0, 0.35);
  }
  * { margin: 0; padding: 0; box-sizing: border-box; }
  html, body { width: 1200px; height: 960px; overflow: hidden; }
  body {
    position: relative;
    background: var(--stage);
    font-family: "Roboto", Arial, sans-serif;
  }
  .card {
    position: absolute;
    left: 313px;
    width: 600px;
    height: 343px;
    box-shadow: 2px 3px 6px var(--shadow);
  }
  /* Front */
  .card-front { top: 113px; background: var(--card-black); color: var(--ink-white); }
  .holder {
    position: absolute; right: 40px; top: 46px; text-align: right;
  }
  .holder-name {
    font-family: "Roboto Condensed", "Arial Narrow", sans-serif;
    font-weight: 500; font-size: 22px; line-height: 24px; letter-spacing: 0.2px;
  }
  .holder-title { font-size: 15px; line-height: 17px; }
  .accent-bar {
    position: absolute; left: 0; top: 173px; width: 28px; height: 137px;
    background: var(--ink-white);
  }
  .address {
    position: absolute; left: 53px; top: 170px;
    font-size: 15px; line-height: 18px; font-style: normal;
  }
  .contacts {
    position: absolute; left: 51px; top: 215px; list-style: none;
    font-size: 14.5px; line-height: 19px;
  }
  .contacts li { display: flex; align-items: center; gap: 9px; }
  .contacts svg { width: 13px; height: 13px; fill: var(--ink-white); flex: none; }
  /* Back */
  .card-back { top: 472px; background: var(--card-white); }
  .brand-name {
    position: absolute; left: 0; right: 0; top: 100px; text-align: center;
    font-weight: 500; font-size: 32px; line-height: 44px; letter-spacing: 4px;
    color: var(--ink-dark);
  }
  .brand-web {
    position: absolute; left: 0; right: 0; top: 292px; text-align: center;
    font-size: 14px; letter-spacing: 2.6px; color: var(--ink-grey);
  }
</style>
</head>
<body>
  <section class="card card-front">
    <div class="holder">
      <div class="holder-name">MELISSA THORNBURY</div>
      <div class="holder-title">Chief Executive Offer</div>
    </div>
    <div class="accent-bar"></div>
    <address class="address">4615 Oakmere Pkwy, Suite 210<br>Raleigh, NC 27654</address>
    <ul class="contacts">
      <li>
        <svg viewBox="0 0 16 16" aria-hidden="true"><path d="M3.5 1l2.5 3-1.5 2c1 2 3 4 5 5l2-1.5 3 2.5-1.5 2.5C8 15 1 8 1 2.5z"/></svg>
        919.362.4178
      </li>
      <li>
        <svg viewBox="0 0 16 16" aria-hidden="true"><path d="M4.5 0h7a1 1 0 0 1 1 1v14a1 1 0 0 1-1 1h-7a1 1 0 0 1-1-1V1a1 1 0 0 1 1-1zm.8 2v10.5h5.4V2zM8 13.3a.9.9 0 1 0 0 1.8.9.9 0 0 0 0-1.8z"/></svg>
        919.537.2846
      </li>
      <li>
        <svg viewBox="0 0 16 16" aria-hidden="true"><path d="M4 1h8v4H4zM1 6h14v6h-2.5v-2h-9v2H1zM4.5 11h7v4h-7z"/></svg>
        919.685.3907
      </li>
      <li>
        <svg viewBox="0 0 16 16" aria-hidden="true"><path d="M1 3h14v1.2L8 9 1 4.2zM1 5.8l7 4.8 7-4.8V13H1z"/></svg>
        mthornbury@brightlinetattooremoval.example
      </li>
      <li>
        <svg viewBox="0 0 16 16" aria-hidden="true"><circle cx="8" cy="8" r="7"/><path d="M5 4c1 1 2 1 2 2.5S5 7 5 9s2 1.5 2 3.5M10 3c0 1.5 1.5 1.5 2 3s-1.5 2-1 4" stroke="#000" stroke-width="1.3" fill="none"/></svg>
        www.brightlinetattooremoval.example
      </li>
    </ul>
  </section>

  <section class="card card-back">
    <div class="brand-name">BRIGHTLINE<br>TATTOO REMOVAL</div>
    <div class="brand-web">www.brightlinetattooremoval.example</div>
  </section>
</body>
</html>
```